Dunmore Roofing

Want a professional looking business card

Industry/Entity Type

Business

Contact Information for Business Card

Paul Dunmore ( Owner) paul@dunmoreroofing-example.com, www.dunmoreroofing-example.com, Adress: 4172 Township road 43 Plantagenet,ON K9X4T2

```html
<!DOCTYPE html>
<html lang="en">
<head>
<meta charset="utf-8">
<title>Dunmore Roofing – Business Card</title>
<link href="https://fonts.googleapis.com/css2?family=Montserrat:wght@400;500;700;800&display=swap" rel="stylesheet">
<style>
  :root {
    --brand-blue: #1f4588;
    --deep-blue: #2a3a94;
    --mid-blue: #2f5ea3;
    --ink-grey: #555a60;
    --band-grey: #77797c;
    --paper: #ffffff;
    --stage: #2a2a2a;
  }
  * { margin: 0; padding: 0; box-sizing: border-box; }
  html, body { width: 1200px; height: 900px; overflow: hidden; }
  body {
    background: var(--stage);
    font-family: "Montserrat", sans-serif;
    position: relative;
  }
  .card {
    position: absolute;
    left: 250px;
    width: 700px;
    height: 400px;
    overflow: hidden;
  }
  /* Back side */
  .card-back {
    top: 35px;
    background: linear-gradient(160deg, var(--deep-blue) 0%, var(--mid-blue) 100%);
  }
  .card-back .world-map {
    position: absolute;
    left: 60px; top: 40px;
    width: 580px; height: 300px;
    border-radius: 40px;
    background: radial-gradient(ellipse at center, rgba(255,255,255,0.10), rgba(255,255,255,0.02) 70%);
  }
  .card-back .brand {
    position: absolute;
    top: 160px; left: 0; right: 0;
    text-align: center;
    color: var(--paper);
    font-weight: 800;
    font-size: 44px;
    letter-spacing: 4px;
    text-transform: uppercase;
  }
  .card-back .web {
    position: absolute;
    bottom: 40px; left: 0; right: 0;
    text-align: center;
    color: var(--paper);
    font-size: 15px;
    letter-spacing: 1.5px;
  }
  /* Front side */
  .card-front {
    top: 465px;
    background: var(--paper);
  }
  .card-front .brand {
    position: absolute;
    top: 42px; left: 46px;
    display: flex; align-items: center; gap: 16px;
    color: var(--brand-blue);
    font-weight: 800;
    font-size: 38px;
    letter-spacing: 3px;
    text-transform: uppercase;
  }
  .card-front .brand-mark {
    width: 48px; height: 48px;
    background: var(--brand-blue);
    flex: none;
  }
  .card-front .edge-tab {
    position: absolute;
    left: -30px; top: 150px;
    width: 56px; height: 60px;
    border-radius: 0 30px 30px 0;
    background: var(--brand-blue);
  }
  .card-front .person {
    position: absolute;
    left: 60px; top: 160px;
  }
  .person .name {
    color: var(--brand-blue);
    font-weight: 700;
    font-size: 24px;
    text-transform: uppercase;
  }
  .person .role {
    color: var(--ink-grey);
    font-size: 19px;
    text-transform: uppercase;
    margin-top: 2px;
  }
  .card-front .contact {
    position: absolute;
    left: 372px; top: 218px;
    color: var(--ink-grey);
    font-size: 15px;
    line-height: 1.45;
  }
  .contact .address { margin-bottom: 12px; }
  .contact .line { display: flex; align-items: center; gap: 12px; }
  .contact .line svg {
    width: 14px; height: 14px; flex: none;
    fill: none; stroke: var(--brand-blue); stroke-width: 2;
  }
  .contact .line svg.solid { fill: var(--brand-blue); stroke: none; }
  .contact .accent { color: var(--brand-blue); }
  .card-front .footer-band {
    position: absolute;
    left: 0; right: 0; bottom: 0;
    height: 44px;
    background: var(--brand-blue);
  }
  .card-front .footer-block {
    position: absolute;
    left: 0; bottom: 0;
    width: 90px; height: 44px;
    background: var(--band-grey);
  }
</style>
</head>
<body>
  <section class="card card-back">
    <div class="world-map" role="img" aria-label="Faint dotted world map across the card background"></div>
    <div class="brand">Dunmore Roofing</div>
    <div class="web">www.dunmoreroofing-example.com</div>
  </section>

  <section class="card card-front">
    <div class="brand"><span class="brand-mark"></span>Dunmore Roofing</div>
    <div class="edge-tab"></div>
    <div class="person">
      <div class="name">Paul Dunmore</div>
      <div class="role">Owner</div>
    </div>
    <div class="contact">
      <div class="address">4172 Township road 43<br>Harrowfield, ON K9X4T2</div>
      <div class="line">
        <svg class="solid" viewBox="0 0 24 24"><path d="M6.6 10.8a15 15 0 0 0 6.6 6.6l2.2-2.2a1 1 0 0 1 1-.25 11.4 11.4 0 0 0 3.6.57 1 1 0 0 1 1 1V20a1 1 0 0 1-1 1A17 17 0 0 1 3 4a1 1 0 0 1 1-1h3.5a1 1 0 0 1 1 1c0 1.25.2 2.45.57 3.57a1 1 0 0 1-.25 1z"/></svg>
        <span>(555)014-2387</span>
      </div>
      <div class="line">
        <svg viewBox="0 0 24 24"><rect x="2" y="5" width="20" height="14" rx="1"/><path d="M2 6l10 7 10-7"/></svg>
        <span>paul@dunmoreroofing-example.com</span>
      </div>
      <div class="line">
        <svg viewBox="0 0 24 24"><circle cx="12" cy="12" r="10"/><ellipse cx="12" cy="12" rx="4.5" ry="10"/><path d="M2 12h20"/></svg>
        <span>www.<span class="accent">dunmoreroofing-example</span>.com</span>
      </div>
    </div>
    <div class="footer-band"></div>
    <div class="footer-block"></div>
  </section>
</body>
</html>
```